Recruitment Site Design

We need a design for the login page, about page, and inner pages of a recruitment site for an oil and gas company. Design should be modern, sleek, professional and colors can be blue, green, white, orange or any other recommended colors.

Please also take into consideration that once the users login, they will need to access a form to fill in their information.

** UPDATE: Kindly provide a design for the inner information page consistent with the outer design. Attached is a picture of the basic structure. ***
Updates

Please provide a design for inner pages as shown in the design brief consistent with the registration page provided. 

Reason: We're extending it to get more inside pages.

Target Market(s)

Professionals looking for a career in the oil and gas industry in the Middle East.

Industry/Entity Type

Oil And Gas

Requirements
Must have
• Sleek design

```html
<!DOCTYPE html>
<html lang="en">
<head>
<meta charset="utf-8">
<title>PetroHire – Careers in Oil and Gas</title>
<link rel="stylesheet" href="https://fonts.googleapis.com/css2?family=Marcellus&family=PT+Sans:ital,wght@0,400;0,700;1,400&display=swap">
<style>
:root{
  --teal:#2aa7b8;
  --teal-nav:#5bc6d6;
  --teal-light:#a3e1ea;
  --teal-box:#59c3d3;
  --dark:#2f2f2f;
  --text:#555;
  --muted:#777;
  --line:#dedede;
  --white:#fff;
}
*{box-sizing:border-box;margin:0;padding:0}
html,body{width:1060px;height:1200px;overflow:hidden}
body{position:relative;background:var(--white);font-family:"PT Sans",Arial,sans-serif;color:var(--text)}
.abs{position:absolute}
.top-strip{left:0;top:0;width:1060px;height:12px;background:var(--dark)}
.header-band{left:0;top:12px;width:1060px;height:126px;background:linear-gradient(#f2f2f2,#fff 40%,#fff)}
.dark-band{left:0;top:138px;width:1060px;height:286px;background:var(--dark)}
.under-band{left:0;top:424px;width:1060px;height:40px;background:linear-gradient(#ececec,#fff)}
.brand{left:78px;top:40px;font-family:"Marcellus",serif;font-size:52px;color:var(--teal);letter-spacing:-1px;line-height:60px}
.search{left:825px;top:62px;width:153px;height:29px;border:1px solid #cfcfcf;border-radius:2px;background:#fff;box-shadow:inset 0 1px 3px rgba(0,0,0,.12);font:italic 11px "PT Sans",sans-serif;color:#aaa;padding:7px 11px}
.search svg{position:absolute;right:10px;top:8px}
.nav{left:78px;top:115px;width:904px;height:47px;display:flex;background:var(--teal-nav);border-bottom:3px solid #3aa9ba}
.nav a{display:flex;align-items:center;justify-content:center;height:44px;color:#1d1d1d;font-size:12.5px;text-decoration:none;border-right:1px solid #43b0c1}
.nav a:last-child{border-right:0}
.nav a.active{background:var(--teal-light)}
.slider{left:78px;top:166px;width:904px;height:288px;background:#e4e4e4;padding:7px 6px}
.slide{position:relative;width:892px;height:276px;background:linear-gradient(180deg,#c6c9ec 0%,#d9dbf0 55%,#8c9cb8 62%,#2c4461 78%,#13253c 100%)}
.slide .rig{position:absolute;right:0;top:0;width:300px;height:276px;background:linear-gradient(90deg,rgba(80,60,60,0),rgba(70,55,55,.65) 40%,rgba(50,40,40,.8))}
.slide h2{position:absolute;left:79px;top:75px;font:400 24px "PT Sans",sans-serif;color:#333}
.dots{position:absolute;left:28px;top:244px;display:flex;gap:8px}
.dots span{width:11px;height:11px;border-radius:50%;background:#fff}
.dots span:first-child{background:var(--teal-nav)}
h3.section{font-family:"Marcellus",serif;font-weight:400;color:var(--teal);font-size:19px}
.welcome{left:78px;top:487px;font-size:24px;color:#666}
.welcome b{font-weight:400;color:var(--teal)}
.copy{font-size:11.5px;line-height:18.4px;text-align:justify;color:var(--text)}
.copy-a{left:78px;top:531px;width:360px}
.copy-a p+p{margin-top:8px;text-indent:3px}
.copy-b{left:78px;top:706px;width:627px}
.photo-frame{left:456px;top:535px;width:249px;height:152px;background:#eee;padding:4px}
.photo-frame div{width:100%;height:100%;background:linear-gradient(120deg,#3e4650,#9aa2ab 45%,#5e6468 70%,#c9cfd3)}
.btn-more{left:78px;top:780px;width:88px;height:32px;border-radius:4px;background:#3c3c3c;color:#fff;font-size:13px;display:flex;align-items:center;justify-content:center;box-shadow:0 1px 2px rgba(0,0,0,.3)}
.vdiv{left:740px;top:489px;width:1px;height:332px;background:var(--line)}
.jobs-title{left:771px;top:490px}
.jobs{left:771px;top:535px;width:215px;list-style:none}
.job{position:absolute;left:0;display:flex;gap:12px}
.thumb{width:75px;height:45px;border:1px solid #ddd;padding:1px;background:#fff}
.thumb div{width:100%;height:100%}
.job strong{display:block;font-weight:400;font-size:13px;color:var(--teal);margin-top:-1px}
.job span{display:block;font-size:12.5px;color:var(--muted);margin-top:3px}
.hr{left:78px;top:859px;width:904px;height:1px;background:var(--line)}
.testi-title{left:78px;top:891px}
.avatar{left:81px;top:940px;width:83px;height:83px;background:#e3e3e3;border:2px solid #efefef}
.quote{left:192px;top:936px;width:513px;font:italic 11px/22px "PT Sans",sans-serif;color:#555;text-align:justify}
.qmark{font:700 17px/1 Georgia,serif;color:#888;font-style:normal;vertical-align:-3px}
.q-open{margin-right:12px}
.q-close{margin-left:14px;vertical-align:-7px}
.client{left:560px;top:1011px;width:142px;text-align:right;font-size:11px;color:var(--teal)}
.newsletter{left:740px;top:880px;width:242px;height:141px;background:var(--teal-box);border-radius:3px}
.newsletter h4{position:absolute;left:31px;top:12px;font:400 16.5px/22px "Marcellus",serif;color:#fff;white-space:nowrap;letter-spacing:-.2px}
.envelope{left:-9px;top:-4px}
.newsletter .field{position:absolute;left:19px;top:53px;width:209px;height:37px;background:#fff;border:1px solid #d6eef2;font:italic 11px "PT Sans",sans-serif;color:#777;padding:11px 15px}
.newsletter .submit{position:absolute;left:154px;top:103px;width:74px;height:27px;border-radius:14px;background:linear-gradient(#fff,#e3e3e3);color:#555;font-size:13px;display:flex;align-items:center;justify-content:center;box-shadow:0 1px 3px rgba(0,0,0,.3)}
.pre-footer{left:0;top:1030px;width:1060px;height:44px;background:linear-gradient(#fff,#ececec)}
.footer{left:0;top:1074px;width:1060px;height:126px;background:var(--dark);color:#ddd}
.fcol{position:absolute;top:22px}
.fcol h5{font-weight:400;font-size:12px;color:#e6e6e6;margin-bottom:8px}
.fcol ul{list-style:none}
.fcol li{font-size:11px;color:#ddd;line-height:16.5px;padding-left:13px;position:relative}
.fcol li::before{content:"";position:absolute;left:1px;top:6px;width:4px;height:4px;border-right:1.5px solid #ddd;border-top:1.5px solid #ddd;transform:rotate(45deg)}
.fdiv{position:absolute;left:740px;top:18px;width:1px;height:91px;background:#555}
.connect{position:absolute;left:769px;top:22px;font-size:12px;color:#e6e6e6;display:flex;align-items:center;gap:6px}
.connect i{display:block;width:22px;height:22px;border-radius:50%;background:#fff;margin-left:4px}
.copyright{position:absolute;left:770px;top:70px;font-size:12px;line-height:20px;color:#e6e6e6}
</style>
</head>
<body>
<div class="abs top-strip"></div>
<div class="abs header-band"></div>
<div class="abs dark-band"></div>
<div class="abs under-band"></div>

<div class="abs brand">PetroHire</div>
<div class="abs search">Search
  <svg width="11" height="11" viewBox="0 0 11 11"><circle cx="4.5" cy="4.5" r="3.3" fill="none" stroke="#aaa" stroke-width="1.3"/><line x1="7" y1="7" x2="10" y2="10" stroke="#aaa" stroke-width="1.5"/></svg>
</div>

<nav class="abs nav">
  <a class="active" style="width:102px">HOME</a>
  <a style="width:120px">ABOUT US</a>
  <a style="width:135px">OUR SERVICES</a>
  <a style="width:85px">JOBS</a>
  <a style="width:125px">COMPANYS</a>
  <a style="width:111px">RESUMES</a>
  <a style="width:130px">CONTACT US</a>
  <a style="width:96px">HELP</a>
</nav>

<section class="abs slider">
  <div class="slide" role="img" aria-label="Offshore oil platform at sea under a lavender dusk sky">
    <div class="rig"></div>
    <h2>Quis autem vel eum iure</h2>
    <div class="dots"><span></span><span></span><span></span><span></span></div>
  </div>
</section>

<h3 class="abs section welcome">Welcome to <b>PetroHire</b></h3>
<div class="abs copy copy-a">
  <p>Sed ut perspiciatis unde omnis iste natus error sit voluptatem accusan tium doloremque laudantium, totam rem aperiam, eaque ipsa quae ab illo inventore veritatis et quasi architecto beatae vitae dicta sunt expli cabo. Nemo enim ipsam voluptatem quia voluptas sit aspernatur aut odit aut fugit, sed quia consequuntur magni dolores eos qui ratione voluptatem sequi nesciunt.</p>
  <p>Neque porro quisquam est, qui dolorem ipsum quia dolor sit amet, con sectetur, adipisci velit, sed quia non numquam.</p>
</div>
<div class="abs photo-frame"><div role="img" aria-label="Oil worker in a hard hat watching a dark smoke plume over a field"></div></div>
<p class="abs copy copy-b">Sed ut perspiciatis unde omnis iste natus error sit voluptatem accusan tium doloremque laudantium, totam rem aperiam, eaque ipsa quae ab illo inventore veritatis et quasi architecto beatae vitae dicta sunt expli cabo. Nemo enim ipsam voluptatem quia voluptas sit aspernatur aut odit aut fugit, sed quia consequuntur magni dolores.</p>
<div class="abs btn-more">View more</div>

<div class="abs vdiv"></div>
<h3 class="abs section jobs-title">Latest Jobs</h3>
<ul class="abs jobs">
  <li class="job" style="top:0"><div class="thumb"><div role="img" aria-label="Offshore rig on blue sea" style="background:linear-gradient(#9cc3e6,#2e5f8f 60%,#16324f)"></div></div><div><strong>Mauris non est turpis</strong><span>Job Type, City Name</span></div></li>
  <li class="job" style="top:65px"><div class="thumb"><div role="img" aria-label="Drilling truck on a desert site" style="background:linear-gradient(#b9cbe0,#d9d2c2 60%,#8d8270)"></div></div><div><strong>Mauris non est turpis</strong><span>Job Type, City Name</span></div></li>
  <li class="job" style="top:130px"><div class="thumb"><div role="img" aria-label="Pump jack against a blue sky" style="background:linear-gradient(#2f6fc0,#6ea4de 60%,#b13a24)"></div></div><div><strong>Mauris non est turpis</strong><span>Job Type, City Name</span></div></li>
  <li class="job" style="top:187px"><div class="thumb"><div role="img" aria-label="Pump jack at orange sunset" style="background:linear-gradient(#e7863a,#f2b061 50%,#3a2518)"></div></div><div><strong>Mauris non est turpis</strong><span>Job Type, City Name</span></div></li>
  <li class="job" style="top:244px"><div class="thumb"><div role="img" aria-label="Supply vessels at sea" style="background:linear-gradient(#cdd9e6,#6f8fae 55%,#2b4d6e)"></div></div><div><strong>Mauris non est turpis</strong><span>Job Type, City Name</span></div></li>
</ul>

<div class="abs hr"></div>

<h3 class="abs section testi-title">Testimonials</h3>
<div class="abs avatar" role="img" aria-label="Client portrait placeholder"></div>
<p class="abs quote"><span class="qmark q-open">“</span>Sed ut perspiciatis unde omnis iste natus error sit voluptatem accusan tium doloremque laudan-tium, totam rem aperiam, eaque ipsa quae ab illo inventore veritatis et quasi architecto beatae vitae dicta sunt expli cabo. Nemo enim ipsam voluptatem quia voluptas.<span class="qmark q-close">”</span></p>
<div class="abs client">Client Name, City</div>

<section class="abs newsletter">
  <svg class="abs envelope" width="36" height="30" viewBox="0 0 36 30"><rect x="4" y="6" width="28" height="19" rx="2" transform="rotate(-14 18 15)" fill="#fff" stroke="#cfcfcf"/><path d="M5 10 L18 17 L31 4" transform="rotate(-14 18 15)" fill="none" stroke="#bbb"/></svg>
  <h4>Subscribe for Newsletter</h4>
  <div class="field">Enter your mail ID</div>
  <div class="submit">SUBMIT</div>
</section>

<div class="abs pre-footer"></div>

<footer class="abs footer">
  <div class="fcol" style="left:83px"><h5>About us</h5><ul><li>Consectetur</li><li>Mauris ideaui</li><li>Aunc vivera ornare</li><li>Nunc convallis</li></ul></div>
  <div class="fcol" style="left:243px"><h5>Services</h5><ul><li>Consectetur</li><li>Mauris ideaui</li><li>Aunc vivera ornare</li><li>Nunc convallis</li></ul></div>
  <div class="fcol" style="left:405px"><h5>Jobs</h5><ul><li>Consectetur</li><li>Mauris ideaui</li><li>Aunc vivera ornare</li><li>Nunc convallis</li></ul></div>
  <div class="fcol" style="left:565px"><h5>Partners</h5><ul><li>Consectetur</li><li>Mauris ideaui</li><li>Aunc vivera ornare</li><li>Nunc convallis</li></ul></div>
  <div class="fdiv"></div>
  <div class="connect">Connect with us :<i></i><i></i><i></i></div>
  <div class="copyright">Copyright © 2012 www.petrohire.net<br>All rights reserved.</div>
</footer>
</body>
</html>
```